Powepoint Templates From Logo

We need 3 Powerpoint templates for use in a variety of presentations we develop and customize. Primary uses of the powerpoint presentations are for printed "pitch books" describing our firm's capabilities and approach (a lot of words with some design elements that we have developed), printed presentations of the results of financial evaluations of our clients (lots of charts and graphs) and as the talking points for speeches.

The design needs to be professional and "solid" to establish that we are capable of selling your multi-million dollar business, but also be a little different to show that we are not just boring MBA's.

Our current website and other materials have been developed internally and leave a great deal to be desired. I have initiated this project to demonstrate how much our look can be improved and, if successful, I hope to do much bigger projects in the future.
Updates

This is my first project and I thaank you all for your participation. Since I am new to this, I don;t know if I am providing the help and feedback as I should. Please feel free to let me know how I can be a better customer.

Target Market(s)

professionals (lawyers, accountaants), business owners, business groups, technology people

Industry/Entity Type

Financial

Requirements
Must have
• our logo
a place where logo of client can be inserted if appropriate
templates for the following pages
title page
standard bullet narrative page
page for charts and graphs to mostly fill the page
Should not have a lot of dark solid color that has to be printed.

Nice to have
• something to perk up the color a little

```html
<!DOCTYPE html>
<html lang="en">
<head>
<meta charset="utf-8">
<title>Title Slide</title>
<link rel="stylesheet" href="https://fonts.googleapis.com/css2?family=Oswald:wght@700&family=Arimo:wght@400;700&display=swap">
<style>
  :root {
    --navy: #0a2c63;
    --navy-deep: #072452;
    --sky: #c5dbf6;
    --sky-pale: #e8f1fc;
    --white: #ffffff;
    --portrait-a: #8a8f99;
    --portrait-b: #3b4250;
  }
  html, body {
    margin: 0;
    padding: 0;
    width: 1200px;
    height: 900px;
    overflow: hidden;
    background: var(--white);
  }
  .slide {
    position: relative;
    width: 1200px;
    height: 900px;
    overflow: hidden;
    background: var(--white);
    font-family: "Arimo", Arial, sans-serif;
  }
  .slide-shapes {
    position: absolute;
    inset: 0;
  }
  .portrait {
    position: absolute;
    left: 166px;
    top: 85px;
    width: 185px;
    height: 236px;
    border-radius: 24px;
    border: 2px solid var(--white);
    box-sizing: border-box;
    background: linear-gradient(160deg, var(--portrait-a), var(--portrait-b));
  }
  .project-title {
    position: absolute;
    right: 38px;
    top: 58px;
    margin: 0;
    font-family: "Oswald", "Arial Narrow", sans-serif;
    font-weight: 700;
    font-size: 56px;
    line-height: 1;
    letter-spacing: 0.5px;
    color: var(--sky);
    -webkit-box-reflect: below -6px linear-gradient(transparent 55%, rgba(255,255,255,0.35));
  }
  .sub-title {
    position: absolute;
    right: 38px;
    top: 426px;
    margin: 0;
    font-weight: 700;
    font-size: 39px;
    color: var(--navy);
  }
  .firm-mark {
    position: absolute;
    left: 62px;
    top: 680px;
    display: flex;
    align-items: center;
    gap: 22px;
  }
  .firm-mark .mark-square {
    width: 88px;
    height: 88px;
    border: 4px solid var(--navy);
    border-radius: 14px;
    box-sizing: border-box;
  }
  .firm-mark .firm-name {
    font-weight: 700;
    font-size: 50px;
    letter-spacing: 1px;
    color: var(--navy);
  }
  .page-label {
    position: absolute;
    right: 12px;
    bottom: 10px;
    margin: 0;
    font-size: 21px;
    color: var(--white);
  }
</style>
</head>
<body>
<main class="slide">
  <svg class="slide-shapes" width="1200" height="900" viewBox="0 0 1200 900" aria-hidden="true">
    <polygon points="0,0 1200,0 1200,240 0,600" fill="var(--navy)"/>
    <polygon points="0,600 1200,240 1200,252 0,612" fill="var(--sky)"/>
    <rect x="0" y="877" width="1200" height="23" fill="var(--sky-pale)"/>
    <polygon points="900,900 1200,792 1200,804 934,900" fill="var(--sky)"/>
    <polygon points="934,900 1200,804 1200,900" fill="var(--navy-deep)"/>
  </svg>

  <div class="portrait" role="img" aria-label="Portrait photograph of the presenter"></div>

  <h1 class="project-title">PROJECT TITLE HERE</h1>
  <p class="sub-title">Sub title here</p>

  <div class="firm-mark">
    <span class="mark-square"></span>
    <span class="firm-name">HALVERN CROSS</span>
  </div>

  <p class="page-label">PAGE 1 OF 2</p>
</main>
</body>
</html>
```